Roofing Contractor business card redesign

I want to redesign my business card with a fresh, eye catching concept

Target Market(s)

Residential Roofing Clients, potential employees, and subcontractors.

Industry/Entity Type

Business

Colors

Designer to choose colors to be used in the design.

Requirements
Nice to have
• I just want something that's more pleasing to the eye. You can use a combination of either / or of my logos.

```html
<!DOCTYPE html>
<html lang="en">
<head>
<meta charset="utf-8">
<title>Steady Hands General Builders – Business Card</title>
<link rel="stylesheet" href="https://fonts.googleapis.com/css2?family=Bebas+Neue&family=Dosis:wght@500;600;700&display=swap">
<style>
  :root {
    --backdrop: #2b2b2b;
    --card-white: #f2f2f2;
    --brown: #3d1510;
    --orange: #e36f24;
    --orange-light: #f4ad3a;
    --yellow: #e9b21b;
    --text-grey: #4a4a4a;
    --divider: #c9c9c9;
    --white: #ffffff;
  }
  * { margin: 0; padding: 0; box-sizing: border-box; }
  html, body { width: 1200px; height: 960px; overflow: hidden; }
  body { background: var(--backdrop); position: relative; font-family: "Dosis", sans-serif; }

  .card { position: absolute; width: 600px; height: 343px; overflow: hidden; }

  /* Front */
  .card-front { left: 320px; top: 103px; background: linear-gradient(135deg, #e4e4e4 0%, var(--card-white) 40%, #f7f7f7 100%); }
  .brand { position: absolute; left: 50px; top: 118px; display: flex; align-items: center; gap: 12px; }
  .brand-mark { width: 46px; height: 46px; border-radius: 50%; background: var(--brown); flex: none; }
  .brand-name { color: var(--brown); font-weight: 700; font-size: 22px; line-height: 1.1; }
  .divider { position: absolute; left: 311px; top: 72px; width: 1px; height: 172px; background: var(--divider); }
  .contact { position: absolute; left: 340px; top: 64px; }
  .person-name { font-family: "Bebas Neue", sans-serif; font-size: 33px; color: var(--brown); line-height: 1; letter-spacing: 0.5px; }
  .person-role { color: var(--orange); font-weight: 500; font-size: 15.5px; line-height: 18px; margin-top: 3px; }
  .address { color: var(--text-grey); font-weight: 500; font-size: 15.5px; line-height: 18px; margin-top: 9px; }
  .lines { list-style: none; margin-top: 8px; }
  .lines li { display: flex; align-items: center; gap: 8px; color: var(--text-grey); font-weight: 500; font-size: 15.5px; line-height: 19px; }
  .lines svg { width: 13px; height: 13px; fill: var(--brown); flex: none; }
  .front-stripes { position: absolute; left: 0; bottom: 0; width: 600px; height: 34px; }
  .front-url { position: absolute; right: 18px; bottom: 8px; color: var(--white); font-weight: 500; font-size: 16px; letter-spacing: 2.6px; }

  /* Back */
  .card-back { left: 317px; top: 488px; background: linear-gradient(135deg, var(--orange-light) 0%, #ea8a2a 30%, var(--orange) 55%, var(--orange) 100%); }
  .back-brand { position: absolute; left: 0; top: 70px; width: 600px; display: flex; flex-direction: column; align-items: center; gap: 14px; }
  .back-mark { width: 188px; height: 188px; border-radius: 50%; background: var(--brown); border: 3px solid var(--white); }
  .back-url { position: absolute; left: 0; width: 600px; top: 292px; text-align: center; color: var(--white); font-weight: 500; font-size: 16px; letter-spacing: 2.6px; }
</style>
</head>
<body>
  <section class="card card-front" aria-label="Business card front">
    <div class="brand">
      <span class="brand-mark"></span>
      <span class="brand-name">Steady Hands<br>General Builders, Inc.</span>
    </div>
    <div class="divider"></div>
    <div class="contact">
      <h1 class="person-name">Dale Morrow</h1>
      <p class="person-role">Apex Certified Roof Inspector<br>Licensed Property Adjuster</p>
      <p class="address">4810 Cedar Bend Drive Suite 110<br>Plano, TX 75024</p>
      <ul class="lines">
        <li><svg viewBox="0 0 24 24"><path d="M6.6 10.8a15.1 15.1 0 0 0 6.6 6.6l2.2-2.2c.3-.3.7-.4 1-.2 1.1.4 2.3.6 3.6.6.6 0 1 .4 1 1V20c0 .6-.4 1-1 1A17 17 0 0 1 3 4c0-.6.4-1 1-1h3.5c.6 0 1 .4 1 1 0 1.3.2 2.5.6 3.6.1.3 0 .7-.2 1z"/></svg>(555) 210-4800</li>
        <li><svg viewBox="0 0 24 24"><path d="M7 1h10a2 2 0 0 1 2 2v18a2 2 0 0 1-2 2H7a2 2 0 0 1-2-2V3a2 2 0 0 1 2-2zm0 3v14h10V4z"/></svg>(555) 318-7261</li>
        <li><svg viewBox="0 0 24 24"><path d="M2 5h20v14H2zm2 2v.5l8 5 8-5V7l-8 5z"/></svg>dale@steadyhandstx.com</li>
      </ul>
    </div>
    <svg class="front-stripes" viewBox="0 0 600 34" aria-hidden="true">
      <polygon points="0,12 186,12 181,20 0,20" fill="var(--yellow)"/>
      <polygon points="189,12 360,12 355,20 184,20" fill="var(--brown)"/>
      <rect x="0" y="20" width="600" height="4" fill="var(--orange)"/>
      <polygon points="375,0 600,0 600,34 352,34" fill="var(--orange)"/>
    </svg>
    <span class="front-url">www.steadyhandstx.com</span>
  </section>

  <section class="card card-back" aria-label="Business card back">
    <div class="back-brand">
      <span class="back-mark" role="img" aria-label="Company emblem area"></span>
    </div>
    <span class="back-url">www.steadyhandstx.com</span>
  </section>
</body>
</html>
```